Online shopping portal - Business Card Design

Brivamart.com.au is a complete shopping experience. Search, compare & buy items from partnered stores & receive cashbash for your purchases and referrals.
Mission
Our mission is to provide a system for entrepreneurs to create an ongoing income, while providing consumers worldwide with a better way to shop.
A product brokerage and Internet marketing company that specialises in One-to-One Marketing, Quellon Oceania is a subsidiary of Dorvex Holdings Global, Inc.
With more than 3 million Preferred Customers and 180,000 Customer Managers worldwide, Dorvex Holdings has generated over $3 billion USD in accumulated retail sales. The Company employs more than 675 people globally with international operations in Australia, United States, Canada, Taiwan, Hong Kong, Mexico & Singapore
Through revolutionary technology and the one-to-one marketing and social shopping Quellon Oceania are leveraging the Internet with the power of people to create the economy of the future.
By providing online shoppers with the products and services they want and need — backed by the Company’s people power — Quellon Oceania is fast becoming the World Wide Web’s ultimate online shopping destination.
As a result, we are changing the way people shop and changing the economic paradigm where anyone can become financially independent by creating their own economy — Made with Goods. Driven by Folks®.
Description
Welcome to a new kind of comparison shopping site where you get PAID cashback to shop!
Simply create an account to start accumulating cash backs each time you make purchases across hundreds of trusted Partner Stores and thousands of your favorite brands through our convenient PixBasket® for one stop shopping.
All merchant stores are backed by GLIMVEN.NET's 100% satisfaction guarantee.

Updates
Project Deadline Extended
Reason: Hi all,  I am extending the deadline as i'm going to be away for my birthday (and may not have time to check before the current deadline anyway)  I figure that the more time i give you the better.

Industry/Entity Type
Online Shopping
Contact Information for Business Card
Business Name: Brivamart.com.au
website: www.brivamart.com.au
Facebook: www.facebook.com/brivamart.com.au.
Email: info@brivamart.com.au
Phone: Lorn on 0487 52 19 64
Requirements
Nice to have
- Create a Brivamart logo

```html
<!DOCTYPE html>
<html lang="en">
<head>
<meta charset="utf-8">
<title>Brivamart Business Card</title>
<link rel="stylesheet" href="https://fonts.googleapis.com/css2?family=Libre+Baskerville&family=Montserrat:wght@400;600&display=swap">
<style>
  :root {
    --navy: #1b1a6b;
    --navy-soft: #4a4996;
    --gold: #a5862a;
    --paper: #ffffff;
    --backdrop: #e9e6e0;
    --ink: #2a2a2a;
    --light: #ffffff;
  }
  * { box-sizing: border-box; margin: 0; padding: 0; }
  html, body { width: 1057px; height: 1200px; overflow: hidden; }
  body {
    background: var(--backdrop);
    font-family: "Montserrat", sans-serif;
    position: relative;
  }
  .card {
    position: absolute;
    left: 78px;
    width: 900px;
    height: 514px;
    background: var(--paper);
    box-shadow: 0 6px 24px rgba(0,0,0,0.18);
    overflow: hidden;
  }
  .card-front { top: 48px; }
  .card-back { top: 638px; }

  .logo {
    position: absolute;
    display: flex;
    align-items: center;
    gap: 12px;
    font-family: "Libre Baskerville", serif;
    color: var(--navy);
    letter-spacing: 3px;
    white-space: nowrap;
  }
  .logo-mark { width: 16px; height: 16px; background: var(--gold); }

  .card-front .logo { top: 170px; left: 0; right: 0; justify-content: center; font-size: 52px; }
  .front-band {
    position: absolute;
    left: 0; right: 0; bottom: 70px; height: 96px;
    background: var(--navy);
    display: flex; align-items: center; justify-content: center;
  }
  .front-band .web {
    color: var(--light);
    font-size: 20px;
    letter-spacing: 5px;
  }

  .name-tag {
    position: absolute;
    left: 0; top: 118px;
    width: 280px; height: 56px;
    background: var(--gold);
    color: var(--light);
    font-size: 24px;
    letter-spacing: 3px;
    display: flex; align-items: center; padding-left: 30px;
    white-space: nowrap;
  }
  .job-title {
    position: absolute;
    left: 30px; top: 186px;
    font-size: 15px;
    letter-spacing: 3px;
    color: var(--ink);
    white-space: nowrap;
  }
  .card-back .logo { left: 310px; top: 160px; font-size: 44px; }

  .back-band {
    position: absolute;
    left: 300px; right: 0; top: 238px; height: 120px;
    background: var(--navy);
  }
  .stripe-motif {
    position: absolute;
    left: 20px; top: 28px;
    width: 84px; height: 64px;
    background: linear-gradient(160deg, var(--navy-soft), var(--navy));
  }
  .contacts {
    position: absolute;
    left: 130px; top: 22px;
    display: grid;
    grid-template-columns: auto auto;
    column-gap: 60px; row-gap: 22px;
  }
  .contact {
    display: flex; align-items: center; gap: 12px;
    color: var(--light);
    font-size: 15px;
    letter-spacing: 1px;
    white-space: nowrap;
  }
  .icon {
    width: 26px; height: 26px;
    background: var(--light);
    display: flex; align-items: center; justify-content: center;
    flex-shrink: 0;
  }
  .address {
    position: absolute;
    left: 430px; top: 390px;
    display: flex; align-items: center; gap: 12px;
    font-size: 15px; letter-spacing: 1px; color: var(--ink);
    white-space: nowrap;
  }
  .address .icon { background: var(--gold); }
</style>
</head>
<body>

<section class="card card-front">
  <div class="logo"><span class="logo-name">BRIVAMART</span><span class="logo-mark"></span></div>
  <div class="front-band"><span class="web">www.brivamart.com.au</span></div>
</section>

<section class="card card-back">
  <div class="name-tag">ALDEN FERRIS</div>
  <div class="job-title">GENERAL MANAGER</div>
  <div class="logo"><span class="logo-name">BRIVAMART</span><span class="logo-mark"></span></div>

  <div class="back-band">
    <div class="stripe-motif" role="img" aria-label="Decorative stripe motif"></div>
    <div class="contacts">
      <div class="contact">
        <span class="icon"><svg width="16" height="16" viewBox="0 0 16 16"><path d="M3 1h3l1 4-2 1a9 9 0 0 0 5 5l1-2 4 1v3c0 1-1 2-2 2A13 13 0 0 1 1 3c0-1 1-2 2-2z" fill="#1b1a6b"/></svg></span>
        <span>0487 52 19 64</span>
      </div>
      <div class="contact">
        <span class="icon"><svg width="16" height="16" viewBox="0 0 16 16"><rect x="1" y="3" width="14" height="10" fill="none" stroke="#1b1a6b" stroke-width="1.6"/><polyline points="1,3 8,9 15,3" fill="none" stroke="#1b1a6b" stroke-width="1.6"/></svg></span>
        <span>info@brivamart.com.au</span>
      </div>
      <div class="contact">
        <span class="icon"><svg width="16" height="16" viewBox="0 0 16 16"><rect x="4" y="1" width="8" height="14" rx="1.5" fill="none" stroke="#1b1a6b" stroke-width="1.6"/><circle cx="8" cy="12" r="1" fill="#1b1a6b"/></svg></span>
        <span>0487 52 19 64</span>
      </div>
      <div class="contact">
        <span class="icon"><svg width="16" height="16" viewBox="0 0 16 16"><g fill="none" stroke="#1b1a6b" stroke-width="1.4"><circle cx="8" cy="8" r="6.5"/><ellipse cx="8" cy="8" rx="3" ry="6.5"/><line x1="1.5" y1="8" x2="14.5" y2="8"/></g></svg></span>
        <span>www.brivamart.com.au</span>
      </div>
    </div>
  </div>

  <div class="address">
    <span class="icon"><svg width="14" height="16" viewBox="0 0 14 16"><path d="M7 1a5 5 0 0 1 5 5c0 4-5 9-5 9S2 10 2 6a5 5 0 0 1 5-5z" fill="#ffffff"/><circle cx="7" cy="6" r="1.8" fill="#a5862a"/></svg></span>
    <span>42 Harbor Lane Level 3 Sydney</span>
  </div>
</section>

</body>
</html>
```